NEW Modern Sleek Business Card for VR Language Startup

Our startup is using VR to lead the next wave of world language education. We need a two-sided business card that introduces the larger organization (Brightloom Language Inc) and our contact info on one side and shows the product, Glimwoorld, on the other side.

Side 1 (contact info)= Brightloom Logo and Contact info (name, title, phone, email)

Side 2 (product)= Glimworld logo, text, and website
Text= Culturally Immersive Language Learning Games
Website= www.glimworld-play.com

Target Market(s)

Education, Technology

Contact Information for Business Card

Contact info will be updated upon approval of the design. For now, put this as a placeholder.

Perry Dunmore
Founder & CEO
pdunmore@quillpost-mail.net
(555)-014-2286

Font styles to use
Other font styles liked:
• Gibson and Century Gothic are the brand fonts

Requirements
Nice to have
• I would love to see cohesion between the design and colors of the two logos. I have attached a few business card designs that I like, so you can get a feel for my preferred style.

```html
<!DOCTYPE html>
<html lang="en">
<head>
<meta charset="utf-8">
<title>Brightloom Language Inc – Business Card</title>
<link rel="stylesheet" href="https://fonts.googleapis.com/css2?family=Montserrat:wght@400;500;600;700&family=Questrial&display=swap">
<style>
  :root {
    --bg: #d3d5d4;
    --orange: #f58a4b;
    --coral: #ef4059;
    --magenta: #b6459b;
    --violet: #6c5bb8;
    --sky: #4fb4e6;
    --band-dark: #1e1e22;
    --band-light: #5ec4ee;
    --ink: #2b2b30;
    --ink-soft: #55565c;
    --accent: #e9304f;
    --paper: #ffffff;
  }
  * { box-sizing: border-box; margin: 0; padding: 0; }
  html, body { width: 1200px; height: 900px; overflow: hidden; }
  body {
    background: var(--bg);
    font-family: "Montserrat", sans-serif;
    display: flex;
    flex-direction: column;
    align-items: center;
    justify-content: center;
    gap: 56px;
  }
  .card {
    width: 620px;
    height: 354px;
    position: relative;
    overflow: hidden;
    box-shadow: 0 10px 24px rgba(0,0,0,0.18);
  }

  /* Product side */
  .card--product {
    background: linear-gradient(170deg, var(--orange) 0%, var(--coral) 32%, var(--magenta) 55%, var(--violet) 78%, var(--sky) 100%);
    color: var(--paper);
  }
  .product-body {
    position: absolute;
    inset: 0 0 42px 0;
    display: flex;
    flex-direction: column;
    align-items: center;
    justify-content: center;
    text-align: center;
  }
  .product-brand {
    display: flex;
    align-items: center;
    gap: 14px;
    font-family: "Questrial", sans-serif;
    font-size: 50px;
    letter-spacing: 0.5px;
    color: var(--paper);
  }
  .product-brand__dot {
    width: 30px; height: 30px;
    border-radius: 50%;
    background: var(--paper);
  }
  .product-tagline {
    margin-top: 14px;
    font-size: 17px;
    font-weight: 700;
    letter-spacing: 0.3px;
  }
  .product-site {
    margin-top: 10px;
    font-size: 15px;
    font-weight: 600;
    letter-spacing: 2px;
    color: #1f6fb8;
  }
  .band {
    position: absolute; left: 0; right: 0;
  }
  .band--dark { bottom: 12px; height: 30px; background: var(--band-dark); }
  .band--light { bottom: 0; height: 12px; background: var(--band-light); }

  /* Contact side */
  .card--contact { background: var(--paper); }
  .contact-decor {
    position: absolute;
    top: 0; right: 40px;
    width: 300px; height: 190px;
    background: linear-gradient(180deg, rgba(108,91,184,0.55) 0%, rgba(233,48,79,0.45) 55%, rgba(245,138,75,0.0) 100%);
    -webkit-mask: linear-gradient(90deg, transparent 0%, #000 25%, #000 75%, transparent 100%);
            mask: linear-gradient(90deg, transparent 0%, #000 25%, #000 75%, transparent 100%);
  }
  .contact-brand {
    position: absolute;
    left: 44px; top: 150px;
    display: flex; align-items: center; gap: 12px;
    font-family: "Questrial", sans-serif;
    font-size: 40px;
    color: var(--ink);
    letter-spacing: 1px;
  }
  .contact-brand__dot {
    width: 26px; height: 26px; border-radius: 50%;
    background: var(--coral);
  }
  .contact-person {
    position: absolute;
    left: 44px; bottom: 40px;
  }
  .contact-person__name {
    font-size: 22px; font-weight: 700; color: var(--accent);
  }
  .contact-person__title {
    margin-top: 2px;
    font-size: 14px; font-weight: 500; color: var(--ink);
  }
  .contact-details {
    position: absolute;
    left: 370px; top: 214px;
    padding-left: 16px;
    border-left: 1.5px solid var(--ink);
    list-style: none;
    font-size: 13px;
    color: var(--ink-soft);
  }
  .contact-details li {
    display: flex; align-items: center; gap: 8px;
    line-height: 22px;
  }
  .contact-details svg { width: 12px; height: 12px; flex: none; }
</style>
</head>
<body>

  <section class="card card--product" aria-label="Product side">
    <div class="product-body">
      <div class="product-brand"><span class="product-brand__dot"></span>Glimworld</div>
      <p class="product-tagline">Culturally Immersive Language Learning Games</p>
      <p class="product-site">www.glimworld-play.com</p>
    </div>
    <div class="band band--dark"></div>
    <div class="band band--light"></div>
  </section>

  <section class="card card--contact" aria-label="Contact side">
    <div class="contact-decor" role="img" aria-label="Decorative fan of coloured lines ending in rings"></div>
    <div class="contact-brand"><span class="contact-brand__dot"></span>Brightloom</div>
    <ul class="contact-details">
      <li>
        <svg viewBox="0 0 12 12" aria-hidden="true"><path fill="#e9304f" d="M2.4 0.8l1.8 2.3-1 1.1c0.7 1.5 1.9 2.7 3.4 3.4l1.1-1 2.3 1.8-1 2c-4.5-0.2-8.1-3.8-8.4-8.4z"/></svg>
        (555)-014-2286
      </li>
      <li>
        <svg viewBox="0 0 12 12" aria-hidden="true"><rect x="0.7" y="2.2" width="10.6" height="7.6" fill="none" stroke="#e9304f" stroke-width="1.2"/><path d="M0.9 2.6L6 6.6l5.1-4" fill="none" stroke="#e9304f" stroke-width="1.2"/></svg>
        pdunmore@quillpost-mail.net
      </li>
    </ul>
    <div class="contact-person">
      <p class="contact-person__name">Perry Dunmore</p>
      <p class="contact-person__title">Founder &amp; CEO</p>
    </div>
  </section>

</body>
</html>
```